Design a homepage graphic to show a system journey

We have a software package for parents to update student information and manage school excursions we have attached a concept we like but are open to other ideas so long as they fit the following criteria.
1 It needs to be landscape across the page
2. They are showing a series of processes, each step has its own colour, see below
2.1 The first process is a parent updating their own and students information and approving excursions
2.2 The school then creates and manages the excursion this includes a compliance component
2.3 The school conducts the activity it should show some activity type pictures
2.4 Students return safely to school
3 There can be text boxes within the image to clarify functionality
4. The picture should make anyone watching it understand there is a series of
linked processes the system provides i.e. a journey
There should be the ability to click on each component to link to a specific part of the pager lower down, e.g if the person wanted to look at the school part by clicking on the school it would take them to more information, that information already exists so is not required.
Please review the attached concept diagram and use this a potential guide.
Schools
1 page

```html
<!DOCTYPE html>
<html lang="en">
<head>
<meta charset="utf-8">
<title>School Excursion Journey</title>
<link href="https://fonts.googleapis.com/css2?family=Roboto:wght@400;700&display=swap" rel="stylesheet">
<style>
  :root {
    --bg: #f7f7f7;
    --ink: #6b6b6b;
    --rule: #b9b9b9;
    --yellow: #f2b705;
    --orange: #ef8a22;
    --red: #e8493f;
    --magenta: #a63b8f;
    --purple: #7a4a91;
    --teal: #0f6e93;
    --cyan: #11a8c6;
    --green: #3bb54a;
    --green-light: #9bd56a;
  }
  html, body { margin: 0; padding: 0; overflow: hidden; background: var(--bg); }
  .journey { display: block; width: 1200px; height: 838px; }
  .step-title { font-family: "Roboto", Arial, sans-serif; font-weight: 700; font-size: 17px; letter-spacing: 0.4px; }
  .step-copy { font-family: "Roboto", Arial, sans-serif; font-weight: 400; font-size: 16px; fill: var(--ink); }
  .leader { fill: none; stroke: var(--rule); stroke-width: 1.2; }
  .road { fill: none; stroke-width: 40; stroke-linecap: butt; }
  .lane { fill: none; stroke: #fff; stroke-width: 2; }
  .stop-ring { fill: #fff; stroke-width: 6; }
  .icon { fill: none; stroke: #222; stroke-width: 1.6; stroke-linecap: round; stroke-linejoin: round; }
  .step-link { cursor: pointer; }
  .step-link:hover .stop-ring { stroke-width: 8; }
</style>
</head>
<body>
<svg class="journey" viewBox="0 0 1400 978" xmlns="http://www.w3.org/2000/svg">
  <defs>
    <filter id="road-shadow" x="-10%" y="-10%" width="120%" height="130%">
      <feDropShadow dx="0" dy="8" stdDeviation="9" flood-color="#000" flood-opacity="0.22"/>
    </filter>
    <linearGradient id="green-fade" x1="0" x2="1" y1="0" y2="0">
      <stop offset="0" stop-color="var(--green)"/>
      <stop offset="1" stop-color="var(--green-light)"/>
    </linearGradient>
    <linearGradient id="activity-photo" x1="0" x2="1" y1="0" y2="1">
      <stop offset="0" stop-color="#5c6470"/>
      <stop offset="0.55" stop-color="#b7a79a"/>
      <stop offset="1" stop-color="#c0433f"/>
    </linearGradient>
  </defs>

  <rect width="1400" height="978" fill="var(--bg)"/>

  <!-- leader lines -->
  <g class="leaders">
    <path class="leader" d="M210 505 V568"/>
    <path class="leader" d="M418 782 V846 H525"/>
    <path class="leader" d="M398 445 V523 H452"/>
    <path class="leader" d="M610 205 V270"/>
    <path class="leader" d="M768 338 V438 H822"/>
    <path class="leader" d="M780 690 V846 H888"/>
    <path class="leader" d="M967 178 V113 H1075"/>
    <path class="leader" d="M1154 532 V597"/>
  </g>

  <!-- road -->
  <g class="road-group" filter="url(#road-shadow)">
    <path class="road" stroke="var(--yellow)" d="M123 450 H280 Q327 450 327 497 V582"/>
    <path class="road" stroke="var(--orange)" d="M327 580 V680 Q327 720 367 720 H470 Q510 720 510 680 V640"/>
    <path class="road" stroke="var(--yellow)" d="M510 642 V598"/>
    <path class="road" stroke="var(--red)" d="M510 600 V398"/>
    <path class="road" stroke="var(--magenta)" d="M510 400 V370 Q510 328 552 328 H655 Q697 328 697 370 V492"/>
    <path class="road" stroke="var(--purple)" d="M697 490 V590 Q697 630 737 630 H835 Q875 630 875 590 V543"/>
    <path class="road" stroke="var(--teal)" d="M875 545 V328"/>
    <path class="road" stroke="var(--cyan)" d="M875 330 V287 Q875 245 917 245 H1018 Q1060 245 1060 287 V357"/>
    <path class="road" stroke="var(--green)" d="M1060 355 V420 Q1060 470 1110 470 H1160"/>
    <path class="road" stroke="url(#green-fade)" d="M1158 470 H1264"/>
  </g>
  <path class="lane" d="M170 450 H280 Q310 450 310 480 V690 Q310 737 357 737 H480 Q527 737 527 690 V360 Q527 345 542 345 H665 Q680 345 680 360 V600 Q680 647 727 647 H845 Q892 647 892 600 V277 Q892 262 907 262 H1028 Q1043 262 1043 277 V430 Q1043 487 1100 487 H1195"/>
  <path d="M125 450 H170" stroke="#fff" stroke-width="2.5" stroke-dasharray="2 4"/>
  <path d="M1197 470 H1262" stroke="#fff" stroke-width="2.5" stroke-dasharray="2 4"/>

  <!-- stops -->
  <a class="step-link" href="#parent-information">
    <circle class="stop-ring" cx="210" cy="450" r="35" stroke="var(--yellow)"/>
    <g class="icon"><path d="M196 440 Q192 460 206 466 M224 440 Q228 460 214 466"/><circle cx="210" cy="442" r="4"/><circle cx="202" cy="447" r="3"/><circle cx="218" cy="447" r="3"/></g>
  </a>
  <a class="step-link" href="#student-information">
    <circle class="stop-ring" cx="418" cy="720" r="35" stroke="var(--orange)"/>
    <g class="icon"><rect x="404" y="706" width="22" height="28"/><rect x="409" y="701" width="22" height="28"/><circle cx="416" cy="712" r="3"/><path d="M411 720 Q416 715 421 720 M413 725 H427"/></g>
  </a>
  <a class="step-link" href="#approving-excursion">
    <circle class="stop-ring" cx="510" cy="522" r="35" stroke="var(--red)"/>
    <g class="icon"><rect x="496" y="506" width="22" height="30"/><path d="M500 513 H514 M500 518 H508"/><circle cx="512" cy="522" r="5"/><path d="M510 522 L512 524 L515 520 M516 532 H528 M522 532 V526"/></g>
  </a>
  <a class="step-link" href="#school-accepts">
    <circle class="stop-ring" cx="610" cy="328" r="35" stroke="var(--magenta)"/>
    <g class="icon"><path d="M594 344 V326 H626 V344 Z M600 326 L610 317 L620 326 M610 317 V309 H617"/><rect x="606" y="336" width="8" height="8"/><path d="M598 331 H602 M618 331 H622"/></g>
  </a>
  <a class="step-link" href="#school-takes-children">
    <circle class="stop-ring" cx="780" cy="636" r="35" stroke="var(--purple)"/>
    <g class="icon"><circle cx="771" cy="627" r="6"/><circle cx="789" cy="627" r="6"/><path d="M761 652 V644 Q771 635 779 644 V652 M781 652 V644 Q789 635 799 644 V652"/></g>
  </a>
  <a class="step-link" href="#school-manages">
    <circle class="stop-ring" cx="875" cy="436" r="35" stroke="var(--teal)"/>
    <g class="icon"><circle cx="875" cy="428" r="8"/><path d="M859 444 L870 440 L880 446 L891 440 M863 438 V448 M887 438 V448"/></g>
  </a>
  <a class="step-link" href="#school-conducts-activity">
    <circle class="stop-ring" cx="967" cy="243" r="35" stroke="var(--cyan)"/>
    <g class="icon"><path d="M955 232 L967 226 L979 232 L967 238 Z M961 235 V241 Q967 245 973 241 V235"/><rect x="952" y="248" width="28" height="5"/><rect x="955" y="253" width="26" height="5"/></g>
  </a>
  <a class="step-link" href="#students-return">
    <circle class="stop-ring" cx="1155" cy="472" r="35" stroke="var(--green)"/>
    <g class="icon"><path d="M1140 480 L1152 466 L1160 468 L1170 460 M1146 486 L1158 476 L1166 478 L1172 470 M1152 466 L1162 476"/></g>
  </a>

  <!-- activity photo -->
  <rect x="1090" y="72" width="174" height="126" fill="#fff"/>
  <rect x="1097" y="79" width="160" height="113" fill="url(#activity-photo)" role="img" aria-label="Photo of students on an excursion bus"/>

  <!-- labels -->
  <a class="step-link" href="#parent-information">
    <text class="step-title" fill="var(--yellow)" text-anchor="middle"><tspan x="210" y="598">PARENT</tspan><tspan x="210" y="618">INFORMATION</tspan></text>
  </a>
  <text class="step-copy" text-anchor="middle"><tspan x="210" y="651">Sed ut perspiciatis unde</tspan><tspan x="210" y="676">omnis iste natus error</tspan><tspan x="210" y="701">sit voluptatem</tspan></text>

  <a class="step-link" href="#approving-excursion">
    <text class="step-title" fill="var(--red)" text-anchor="middle"><tspan x="397" y="323">APPROVING</tspan><tspan x="397" y="343">EXCURSION</tspan></text>
  </a>
  <text class="step-copy" text-anchor="middle"><tspan x="397" y="376">Sed ut perspiciatis unde</tspan><tspan x="397" y="401">omnis iste natus error</tspan><tspan x="397" y="426">sit voluptatem</tspan></text>

  <a class="step-link" href="#school-accepts">
    <text class="step-title" fill="var(--magenta)" text-anchor="middle"><tspan x="610" y="84">THE SCHOOL ACCEPTS</tspan><tspan x="610" y="104">ALL THE UPDATE</tspan></text>
  </a>
  <text class="step-copy" text-anchor="middle"><tspan x="610" y="137">Sed ut perspiciatis unde</tspan><tspan x="610" y="162">omnis iste natus error</tspan><tspan x="610" y="187">sit voluptatem</tspan></text>

  <a class="step-link" href="#school-manages">
    <text class="step-title" fill="var(--teal)" text-anchor="middle"><tspan x="762" y="217">THE SCHOOL MANAGES</tspan><tspan x="762" y="237">THE EXCURSION</tspan></text>
  </a>
  <text class="step-copy" text-anchor="middle"><tspan x="762" y="270">Sed ut perspiciatis unde</tspan><tspan x="762" y="295">omnis iste natus error</tspan><tspan x="762" y="320">sit voluptatem</tspan></text>

  <a class="step-link" href="#school-conducts-activity">
    <text class="step-title" fill="var(--cyan)"><tspan x="1091" y="234">THE SCHOOL</tspan><tspan x="1091" y="254">CONDUCTS ACTIVITY</tspan></text>
  </a>
  <text class="step-copy"><tspan x="1091" y="287">Sed ut perspiciatis unde</tspan><tspan x="1091" y="312">omnis iste natus error</tspan><tspan x="1091" y="337">sit voluptatem</tspan></text>

  <a class="step-link" href="#students-return">
    <text class="step-title" fill="var(--green)" text-anchor="middle"><tspan x="1154" y="626">STUDENTS RETURN</tspan><tspan x="1154" y="646">TO THE SCHOOL</tspan></text>
  </a>
  <text class="step-copy" text-anchor="middle"><tspan x="1154" y="679">Sed ut perspiciatis unde</tspan><tspan x="1154" y="704">omnis iste natus error</tspan><tspan x="1154" y="729">sit voluptatem</tspan></text>

  <a class="step-link" href="#student-information">
    <text class="step-title" fill="var(--orange)"><tspan x="546" y="798">STUDENT</tspan><tspan x="546" y="818">INFORMATION</tspan></text>
  </a>
  <text class="step-copy"><tspan x="547" y="851">Sed ut perspiciatis unde</tspan><tspan x="547" y="876">omnis iste natus error</tspan><tspan x="547" y="901">sit voluptatem</tspan></text>

  <a class="step-link" href="#school-takes-children">
    <text class="step-title" fill="var(--purple)"><tspan x="906" y="798">THE SCHOOL TAKES THE</tspan><tspan x="906" y="818">CHILDREN TO THE EXCURSION</tspan></text>
  </a>
  <text class="step-copy"><tspan x="907" y="851">Sed ut perspiciatis unde</tspan><tspan x="907" y="876">omnis iste natus error</tspan><tspan x="907" y="901">sit voluptatem</tspan></text>
</svg>
</body>
</html>
```